Business card design needed

I would like a one sided black business card with the information provided above. Refer to my website www.brightvolleyracquets.com.au for an example of colors I have used for my site, would like to keep this consistent for my business cards also, I will upload my logo below.

I am a new small business that provides tennis customers with racquet re stringing, tennis strings and accessories.

Industry/Entity Type

Small Business

Contact Information for Business Card

Bright Volley Tennis

Owen Whitby
Managing Director

brightvolleyracquets@mailbox.example
www.brightvolleyracquets.com.au
0491 726 305

Racquet Restringing/Tennis Strings/Accessories

Requirements
Must have
• Must have my logo and card must be black

```html
<!DOCTYPE html>
<html lang="en">
<head>
<meta charset="utf-8">
<title>Bright Volley Tennis – Business Card</title>
<link rel="stylesheet" href="https://fonts.googleapis.com/css2?family=Source+Sans+3:ital,wght@0,400;0,600;0,700;1,700&display=swap">
<style>
  :root {
    --backdrop: #e6e3de;
    --card: #030505;
    --lime: #b8cf2f;
    --white: #ffffff;
  }
  * { margin: 0; padding: 0; box-sizing: border-box; }
  html, body {
    width: 1200px;
    height: 750px;
    overflow: hidden;
    background: var(--backdrop);
    font-family: "Source Sans 3", "Myriad Pro", Arial, sans-serif;
  }
  .card {
    position: absolute;
    left: 75px;
    top: 75px;
    width: 1050px;
    height: 600px;
    background: var(--card);
    border-radius: 42px;
  }
  .brand {
    position: absolute;
    left: 40px;
    top: 92px;
    display: flex;
    align-items: center;
    gap: 16px;
  }
  .brand-dot {
    width: 46px;
    height: 46px;
    border-radius: 50%;
    background: var(--lime);
  }
  .brand-name {
    color: var(--lime);
    font-weight: 700;
    font-size: 46px;
    letter-spacing: 0.5px;
    line-height: 1;
  }
  .contact {
    position: absolute;
    left: 41px;
    top: 431px;
    color: var(--white);
  }
  .contact-name {
    color: var(--lime);
    font-size: 34px;
    font-weight: 700;
    line-height: 1;
  }
  .contact-role {
    font-size: 26px;
    font-weight: 400;
  }
  .contact-line {
    font-size: 25px;
    font-weight: 400;
    line-height: 1;
    margin-top: 18px;
  }
  .contact-line:first-of-type { margin-top: 20px; }
  .label {
    font-weight: 700;
    font-style: italic;
  }
  .divider { margin: 0 10px; }
</style>
</head>
<body>
  <div class="card">
    <div class="brand">
      <span class="brand-dot"></span>
      <span class="brand-name">BRIGHT VOLLEY TENNIS</span>
    </div>

    <div class="contact">
      <p class="contact-name">Owen Whitby - <span class="contact-role">Managing Director</span></p>
      <p class="contact-line"><span class="label">phone</span> 0491 726 305</p>
      <p class="contact-line"><span class="label">email</span> brightvolleyracquets@mailbox.example<span class="divider">|</span><span class="label">web</span> www.brightvolleyracquets.com.au</p>
    </div>
  </div>
</body>
</html>
```